National Water and Fire Restoration, Multi Surface Cleaning, Carpet Cleaning Business Needs a Websi

We need a new fresh website for our business. There are multiple services we offer and we need a fresh corporate website that represents us better. We start from cleaning carpet and tiles, to upholstery and curtains, to completely clean all contents and building materials after a fire, or completely dry out a home or business after a major or minor flood event. We are open to all concepts as we want to create a new look, maybe even logo, signage, vehicle signage, uniforms.
We are open to new colours etc.

Go to www.brightvaleclean.com.au for current logo and all other past ideas

Reason: I need to see more quality designs to sink my teeth into

Target Market(s)

The target market is everyone of all walks of life

Industry/Entity Type

Business

Number of Pages Required

3 page

Font styles to use
Sans Serif

Requirements
Must have
• Home page
• Services page
• Contact us page
• The rest is up to your imagination
• ***This is design only - NO CODING REQUIRED***
Nice to have
• Pictures

```html
<!DOCTYPE html>
<html lang="en">
<head>
<meta charset="utf-8">
<title>Brightvale Clean – Cleaning Services</title>
<link href="https://fonts.googleapis.com/css2?family=Open+Sans:wght@400;600;700;800&display=swap" rel="stylesheet">
<style>
:root{
  --navy:#1c3c78;
  --navy-dark:#142c5a;
  --blue:#1f6fb8;
  --sky:#3a8fd6;
  --red:#d5202a;
  --ink:#333;
  --muted:#777;
  --line:#e2e2e2;
  --panel:#f4f5f7;
  --footer:#26282c;
  --footer-dark:#1b1c1f;
}
*{box-sizing:border-box;margin:0;padding:0}
html,body{width:1200px;height:2356px;overflow:hidden}
body{font-family:'Open Sans',Arial,sans-serif;color:var(--ink);background:#fff;font-size:13px;line-height:1.55}
.wrap{width:1136px;margin:0 auto;position:relative}

/* header */
.site-header{height:120px;display:flex;align-items:center;justify-content:space-between}
.brand{display:flex;align-items:center;gap:12px}
.brand-mark{width:46px;height:46px;background:var(--blue);border-radius:50%}
.brand-name{font-weight:800;font-size:30px;color:var(--navy);line-height:1}
.brand-sub{font-size:11px;letter-spacing:3px;color:var(--muted);margin-top:4px;font-weight:600}
.header-contact{text-align:right}
.header-contact .row{display:flex;gap:10px;justify-content:flex-end}
.pill{border:1px solid var(--line);padding:5px 12px;font-size:14px;font-weight:700;color:var(--navy);border-radius:3px;display:flex;align-items:center;gap:6px}
.pill.mail{font-weight:400;font-size:12px;color:var(--muted)}
.tagline{margin-top:10px;font-weight:800;font-size:16px;color:var(--blue)}
.tagline b{color:var(--red)}

/* nav */
.main-nav{height:34px;background:var(--navy);display:flex}
.main-nav .home{width:52px;background:var(--red);display:flex;align-items:center;justify-content:center}
.main-nav a{color:#fff;text-decoration:none;font-size:12px;font-weight:700;padding:0 22px;display:flex;align-items:center;border-right:1px solid #2e5294}

/* hero */
.hero{height:406px;display:flex}
.hero-photo{width:668px;background:linear-gradient(135deg,#c9b49a,#efe6da 55%,#b3a08a)}
.hero-panel{flex:1;background:linear-gradient(#fbfbfb,#eef0f3);padding:46px 40px}
.hero-panel h2{color:var(--red);font-size:34px;font-weight:800;line-height:1.1}
.checks{list-style:none;margin:18px 0}
.checks li{font-size:19px;font-weight:700;color:var(--navy);display:flex;align-items:center;gap:10px;margin-bottom:6px}
.tick{width:20px;height:20px;background:var(--red);display:inline-flex;align-items:center;justify-content:center}
.offer{color:var(--blue);font-weight:800;font-size:22px;line-height:1.25}
.btn-red{display:inline-block;margin-top:16px;background:var(--red);color:#fff;font-weight:800;font-size:22px;padding:10px 26px;border-radius:4px}

/* welcome */
.welcome{padding:50px 0 60px;text-align:center}
.section-title{font-size:28px;font-weight:700;color:var(--navy)}
.section-title span{color:var(--red)}
.rule{width:300px;height:1px;background:var(--line);margin:8px auto;position:relative}
.welcome .lead{font-size:14px;font-weight:700;color:var(--navy);letter-spacing:.5px}
.welcome .lead em{font-style:normal;background:var(--blue);color:#fff;padding:0 6px}
.welcome p.body{text-align:left;margin:14px 0 18px;font-size:13px;color:#555}
.welcome p.body b{color:var(--red)}
.btn-blue{display:inline-block;background:var(--blue);color:#fff;font-size:12px;font-weight:600;padding:6px 16px;border-radius:3px}

/* services */
.services{padding:12px 0 50px;text-align:center}
.cards{display:flex;gap:22px;margin-top:24px;text-align:left}
.card{flex:1;border:1px solid var(--line);background:#fff}
.card h3{background:var(--sky);color:#fff;font-size:14px;font-weight:700;text-align:center;padding:8px}
.card .photo{height:190px}
.card p{font-size:11px;color:var(--muted);padding:10px 12px 4px}
.card .more{font-size:12px;font-weight:700;color:var(--navy);padding:0 12px 12px}
.p-carpet{background:linear-gradient(135deg,#6d7f99,#b9c3d1)}
.p-uphol{background:linear-gradient(135deg,#8b6f55,#d2c0a6)}
.p-leather{background:linear-gradient(135deg,#5a3f2f,#a77f5c)}
.p-rug{background:linear-gradient(135deg,#7f3c30,#c99a70)}

/* three columns */
.trio{display:flex;gap:32px;padding:20px 0 30px;border-top:1px solid var(--line)}
.col{flex:1}
.col h3{font-size:24px;font-weight:700;color:var(--navy);padding-bottom:8px;border-bottom:2px solid var(--line);margin-bottom:14px}
.col h3 span{color:var(--red)}
.schedule-box{height:190px;background:linear-gradient(135deg,#1a5aa8,#4da0e0);padding:20px 22px;color:#fff;position:relative}
.schedule-box .cta{font-weight:800;font-size:20px;line-height:1.2;width:60%}
.schedule-box .save{display:inline-block;margin-top:12px;background:var(--red);font-weight:800;font-size:20px;padding:3px 12px}
.schedule-box .figure{position:absolute;right:0;bottom:0;width:120px;height:165px;background:linear-gradient(#2c6cb8,#174e94)}
.water-photo{height:120px;background:linear-gradient(135deg,#4c8fbf,#c5dceb);position:relative}
.water-photo .hotline{position:absolute;left:0;right:0;bottom:0;background:rgba(20,44,90,.85);color:#fff;font-size:12px;font-weight:700;padding:6px 10px}
.water-photo .hotline b{color:#ffcf3a}
.bullets{display:grid;grid-template-columns:1fr 1fr;gap:8px 14px;margin-top:16px;list-style:none}
.bullets li{font-size:12px;color:#555;padding-left:14px;position:relative}
.bullets li:before{content:"";position:absolute;left:0;top:6px;width:6px;height:6px;background:var(--blue);border-radius:50%}
.why{list-style:none}
.why li{display:flex;align-items:center;gap:12px;font-size:13px;color:#444;font-weight:600;padding:4px 0;border-bottom:1px solid #f0f0f0}
.why .ico{width:22px;height:22px;background:var(--blue);border-radius:3px;display:inline-flex;align-items:center;justify-content:center}

/* testimonials */
.testimonials{padding:10px 0 30px;display:flex;gap:40px}
.testimonials .main{flex:1}
.testimonials h3{font-size:24px;font-weight:700;color:var(--navy);border-bottom:2px solid var(--line);padding-bottom:8px;margin-bottom:20px}
.quote{display:flex;gap:22px}
.avatar{width:110px;height:110px;border-radius:50%;background:linear-gradient(#8fa7c4,#3e5f8c);flex:none}
.quote p{font-size:12px;color:#666;font-style:italic}
.quote .who{color:var(--blue);font-weight:700;font-size:13px;margin-top:12px}
.dots{display:flex;gap:6px;justify-content:flex-end;margin-top:10px}
.dots i{width:9px;height:9px;border-radius:50%;background:#ccc}
.dots i.on{background:var(--blue)}
.seal-area{width:330px;height:200px;background:linear-gradient(135deg,#e9e9e9,#fafafa);display:flex;align-items:center;justify-content:center}
.seal{width:120px;height:120px;border-radius:50%;background:var(--red)}

/* partners */
.partners{margin-top:30px}
.partners h3{font-size:24px;font-weight:700;color:var(--navy);border-bottom:2px solid var(--line);padding-bottom:8px}
.partners h3 span{color:var(--red)}
.partner-row{display:flex;justify-content:space-between;align-items:center;height:72px;padding:0 12px}
.partner-row span{font-size:24px;font-weight:800;color:#222}

/* footer */
.site-footer{position:absolute;left:0;right:0;top:2148px;height:208px;background:var(--footer);color:#bbb}
.site-footer .wrap{display:flex;gap:40px;padding-top:22px}
.site-footer h4{color:#fff;font-size:14px;font-weight:700;margin-bottom:10px}
.links{display:grid;grid-template-columns:1fr 1fr;gap:2px 30px;list-style:none;font-size:12px}
.links li:before{content:"› ";color:var(--sky)}
.fcol{width:220px}
.fcol.links-col{width:270px}
.contact p{font-size:12px;line-height:1.7}
.news p{font-size:12px}
.news .field{display:flex;margin-top:8px}
.news .field div{flex:1;height:26px;background:#fff;border-radius:2px 0 0 2px}
.news .field span{background:var(--blue);color:#fff;font-size:11px;padding:4px 10px}
.flogo{margin-left:auto;text-align:right}
.flogo .brand-name{color:#fff;font-size:22px}
.social{display:flex;gap:6px;justify-content:flex-end;margin-top:14px}
.social i{width:22px;height:22px;border-radius:50%;background:#555}
.copy{font-size:11px;margin-top:10px}
.footer-bar{position:absolute;bottom:0;left:0;right:0;height:24px;background:var(--footer-dark)}
</style>
</head>
<body>
<div class="wrap">
  <header class="site-header">
    <div class="brand">
      <div class="brand-mark"></div>
      <div>
        <div class="brand-name">BRIGHTVALE CLEAN</div>
        <div class="brand-sub">CLEANING SERVICES</div>
      </div>
    </div>
    <div class="header-contact">
      <div class="row">
        <div class="pill"><svg width="14" height="14" viewBox="0 0 24 24"><path fill="#1c3c78" d="M6.6 10.8a15 15 0 006.6 6.6l2.2-2.2c.3-.3.7-.4 1-.2 1.1.4 2.3.6 3.6.6.6 0 1 .4 1 1V20c0 .6-.4 1-1 1A17 17 0 013 4c0-.6.4-1 1-1h3.5c.6 0 1 .4 1 1 0 1.3.2 2.5.6 3.6.1.3 0 .7-.2 1z"/></svg>07 4000 1234</div>
        <div class="pill mail">hello@brightvaleclean.com.au</div>
      </div>
      <div class="tagline"><b>CLEAN</b> - REFRESHED - <b>SAFE</b> for YOU!</div>
    </div>
  </header>

  <nav class="main-nav">
    <div class="home"><svg width="18" height="16" viewBox="0 0 24 22"><path fill="#fff" d="M12 0L0 11h3v11h7v-7h4v7h7V11h3z"/></svg></div>
    <a>ABOUT US</a><a>SERVICES</a><a>COMMERCIAL</a><a>SCHEDULE &amp; JOB</a><a>REFERRAL PROGRAM</a><a>CONTACT US</a><a>LINKS</a>
  </nav>

  <section class="hero">
    <div class="hero-photo" role="img" aria-label="Family relaxing together on a freshly cleaned carpet"></div>
    <div class="hero-panel">
      <h2>PROFESSIONAL CLEANERS</h2>
      <ul class="checks">
        <li><span class="tick"><svg width="12" height="12" viewBox="0 0 12 12"><path d="M1 6l3 3 7-7" stroke="#fff" stroke-width="2" fill="none"/></svg></span>CARPETS</li>
        <li><span class="tick"><svg width="12" height="12" viewBox="0 0 12 12"><path d="M1 6l3 3 7-7" stroke="#fff" stroke-width="2" fill="none"/></svg></span>RUGS</li>
        <li><span class="tick"><svg width="12" height="12" viewBox="0 0 12 12"><path d="M1 6l3 3 7-7" stroke="#fff" stroke-width="2" fill="none"/></svg></span>FLOORS AND FINE FABRICS</li>
      </ul>
      <div class="offer">OUR NEW EXCLUSIVE INTERNET<br>OFFERS SAVE $$$</div>
      <div class="btn-red">SIGN UP NOW</div>
    </div>
  </section>

  <section class="welcome">
    <h2 class="section-title">Welcome To <span>BRIGHTVALE CLEAN</span></h2>
    <div class="rule"></div>
    <div class="lead">TO PROVID YOU WITH THE MOST OUTSTANDING · SERVICE EXPERIENCE <em>EVER!</em></div>
    <p class="body"><b>Brightvale Clean Services</b> is a professional, full-service carpet, floor, fabric care company serving the North Queensland areas including Cairns, Tablelands, Port Douglas and Mission Beach. Brightvale Clean Cleaning has been in business since 1996. At Brightvale Clean Services, we take pride in our reputation, experience, education, systems, and guarantee. Brightvale Clean Services is an industry board certified firm, the world's most recognised body of certification for carpet and upholstery cleaners.</p>
    <div class="btn-blue">Read More ›</div>
  </section>

  <section class="services">
    <h2 class="section-title">Our <span>Services</span></h2>
    <div class="rule"></div>
    <div class="cards">
      <article class="card"><h3>CARPET CLEANING</h3><div class="photo p-carpet" role="img" aria-label="Carpet being steam cleaned"></div><p>Deep hot water extraction lifts dirt, stains and allergens from every fibre of your carpet.</p><div class="more">Read More ›</div></article>
      <article class="card"><h3>UPHOLSTERY CLEANING</h3><div class="photo p-uphol" role="img" aria-label="Sofa upholstery being cleaned"></div><p>Gentle methods suited to each fabric bring lounges and chairs back to fresh condition.</p><div class="more">Read More ›</div></article>
      <article class="card"><h3>LEATHER CLEANING</h3><div class="photo p-leather" role="img" aria-label="Leather couch being conditioned"></div><p>Careful cleaning and conditioning keeps your leather soft, supple and protected longer.</p><div class="more">Read More ›</div></article>
      <article class="card"><h3>RUG CLEANING</h3><div class="photo p-rug" role="img" aria-label="Patterned rug after cleaning"></div><p>Fine and oriental rugs are washed by hand with safe products that protect colours.</p><div class="more">Read More ›</div></article>
    </div>
  </section>

  <section class="trio">
    <div class="col">
      <h3>Cleaning <span>Schedule</span></h3>
      <div class="schedule-box">
        <div class="cta">CLICK HERE TO SCHEDULE YOUR CLEANING TODAY</div>
        <div class="save">SAVE 20%</div>
        <div class="figure" role="img" aria-label="Technician in uniform"></div>
      </div>
    </div>
    <div class="col">
      <h3>Water <span>Damage</span></h3>
      <div class="water-photo" role="img" aria-label="Flooded room being dried out">
        <div class="hotline">Click here for <b>EMERGENCY HOTLINE</b></div>
      </div>
      <ul class="bullets">
        <li>Flood Dry Out</li><li>Mould Removal</li><li>Odour Control</li><li>Content Restore</li>
      </ul>
    </div>
    <div class="col">
      <h3>Why <span>Choose Us</span></h3>
      <ul class="why">
        <li><span class="ico"><svg width="12" height="12" viewBox="0 0 12 12"><path d="M1 6l3 3 7-7" stroke="#fff" stroke-width="2" fill="none"/></svg></span>Reputation</li>
        <li><span class="ico"><svg width="12" height="12" viewBox="0 0 12 12"><path d="M1 6l3 3 7-7" stroke="#fff" stroke-width="2" fill="none"/></svg></span>Experience</li>
        <li><span class="ico"><svg width="12" height="12" viewBox="0 0 12 12"><path d="M1 6l3 3 7-7" stroke="#fff" stroke-width="2" fill="none"/></svg></span>Education &amp; Certification</li>
        <li><span class="ico"><svg width="12" height="12" viewBox="0 0 12 12"><path d="M1 6l3 3 7-7" stroke="#fff" stroke-width="2" fill="none"/></svg></span>Cleaning Systems</li>
        <li><span class="ico"><svg width="12" height="12" viewBox="0 0 12 12"><path d="M1 6l3 3 7-7" stroke="#fff" stroke-width="2" fill="none"/></svg></span>First Class Customer Service</li>
        <li><span class="ico"><svg width="12" height="12" viewBox="0 0 12 12"><path d="M1 6l3 3 7-7" stroke="#fff" stroke-width="2" fill="none"/></svg></span>100% Money Back Guarantee</li>
      </ul>
    </div>
  </section>

  <section class="testimonials">
    <div class="main">
      <h3>Client <span style="color:var(--red)">Testimonials</span></h3>
      <div class="quote">
        <div class="avatar" role="img" aria-label="Client portrait"></div>
        <div>
          <p>“The team arrived on time, explained every step and left our carpets looking brand new. The lounge smells fresh and the old stains are completely gone. Friendly, careful and very professional staff — we will certainly book again and recommend them to all our friends and neighbours.”</p>
          <div class="who">Mr. Daniel Hart</div>
        </div>
      </div>
      <div class="dots"><i class="on"></i><i></i><i></i><i></i></div>
    </div>
    <div class="seal-area" role="img" aria-label="Years of service certificate seal"><div class="seal"></div></div>
  </section>

  <section class="partners">
    <h3>Our <span>Partner</span></h3>
    <div class="partner-row">
      <span>Softfleece</span><span>Fibrelux</span><span>TruSteam</span><span>AirDry Pro</span><span>Greenfern</span>
    </div>
  </section>
</div>

<footer class="site-footer">
  <div class="wrap">
    <div class="fcol links-col">
      <h4>Quick Links</h4>
      <ul class="links">
        <li>Home</li><li>Schedule &amp; Job</li><li>About Us</li><li>Referral Program</li><li>Services</li><li>Contact Us</li><li>Commercial</li><li>Links</li>
      </ul>
    </div>
    <div class="fcol contact">
      <h4>Contact Details</h4>
      <p>Monday to Friday<br>ABN 12 345 678 901<br>PO Box 100, Cairns QLD 4870<br>Office 07 4000 1234<br>www.brightvaleclean.com.au</p>
    </div>
    <div class="fcol news">
      <h4>Newsletter</h4>
      <p>Subscribe to our newsletter to receive our special offers and news.</p>
      <div class="field"><div></div><span>Subscribe</span></div>
    </div>
    <div class="flogo">
      <div class="brand-name">BRIGHTVALE CLEAN</div>
      <div class="social"><i></i><i></i><i></i><i></i></div>
      <div class="copy">© 2014 Brightvale Clean</div>
    </div>
  </div>
  <div class="footer-bar"></div>
</footer>
</body>
</html>
```